NZ First of it's kind solutions directory and marketplace for busy Mums needs a business card design

We need a business card design for our new nationwide business in NZ (long term plans to go global). We provide solutions to the everyday challenges that busy Mums face by connecting them with quality communities and suppliers of carefully selected, relevant products and services. We sell direct via our online marketplace. The final design should communicate our values of inclusivity, quality and smart solutions. Colours should incorporate our logo colour palette of #477077 and #6ba8b2. Our website is at https://www.brightnestmums.example

Target Market(s)

busy Mums, Age 28 – 50, female, income over $100K, location main centres NZ primarily but NZ wide. Is likely juggling work or career with a young family. Probably had hobbies which have fallen by the wayside.
-Wants to succeed in her chosen career without compromising on family life
-to successfully juggle her career without feeling like she is compromising her children
- Is time poor, something always has to give and it’s generally her health (she’ll stay up late, get stressed)
- probably ex corporate or professional career. Has discretional income

Industry/Entity Type

Business

Contact Information for Business Card

Lena Forbisher, Founder, BrightNestMums.example (Strapline Tap; Gather; Sorted), 47 Kowhai Terrace, Ellerslie, Auckland 1051, New Zealand. Mob: 021 483 517 Ph: +64 (0)9 571 4860

Font styles to use
Other font styles liked:
• Raleway, and/or Architects Daughter

Colors
00a990
33b8a4
86cfc6
cfeae6

Requirements
Must have
• the above details, streamline. the logo and colours associated with those logos
Should not have
• foil or metallic colours

```html
<!DOCTYPE html>
<html lang="en">
<head>
<meta charset="utf-8">
<title>BrightNestMums – Business Card</title>
<link rel="stylesheet" href="https://fonts.googleapis.com/css2?family=Roboto:wght@400;700&family=Roboto+Condensed:wght@400;700&display=swap">
<style>
  :root {
    --brand-deep: #477077;
    --brand-light: #6ba8b2;
    --card-white: #f2f2f2;
    --text-body: #4a4a4a;
    --backdrop: #262626;
    --on-dark: #ffffff;
  }
  * { margin: 0; padding: 0; box-sizing: border-box; }
  html, body {
    width: 1200px; height: 960px; overflow: hidden;
    background: var(--backdrop);
  }
  .canvas { position: relative; width: 1200px; height: 960px; }

  .card {
    position: absolute;
    width: 600px; height: 343px;
    overflow: hidden;
  }
  .card--front { left: 314px; top: 113px; background: var(--card-white); }
  .card--back  { left: 311px; top: 472px; background: var(--brand-deep); }

  .wordmark {
    position: absolute; left: 34px; top: 38px;
    display: flex; align-items: center; gap: 10px;
  }
  .wordmark__dot {
    width: 30px; height: 30px; border-radius: 50%;
    background: var(--brand-deep);
  }
  .wordmark__name {
    font-family: "Roboto", Arial, sans-serif;
    font-weight: 700; font-size: 28px; letter-spacing: -0.5px;
    color: var(--brand-deep);
  }

  .person { position: absolute; left: 36px; top: 126px; }
  .person__name {
    font-family: "Roboto Condensed", Arial, sans-serif;
    font-weight: 700; font-size: 22px; color: var(--brand-deep);
    text-transform: uppercase; line-height: 1.1;
  }
  .person__role {
    font-family: "Roboto Condensed", Arial, sans-serif;
    font-size: 15px; color: var(--brand-light);
    text-transform: uppercase; letter-spacing: 0.5px; margin-top: 2px;
  }

  .address, .contacts {
    position: absolute; left: 36px;
    font-family: "Roboto", Arial, sans-serif;
    font-size: 14.5px; line-height: 18px; color: var(--text-body);
  }
  .address { top: 191px; }
  .contacts { top: 257px; list-style: none; }
  .contacts li { display: flex; align-items: center; gap: 8px; height: 19px; }
  .contacts svg { width: 13px; height: 13px; fill: var(--brand-deep); flex: none; }

  .feature-circle {
    position: absolute; left: 377px; top: 82px;
    width: 196px; height: 196px; border-radius: 50%;
    background: var(--brand-deep);
  }

  .back-circle {
    position: absolute; left: 202px; top: 60px;
    width: 196px; height: 196px; border-radius: 50%;
    background: var(--on-dark); opacity: 0.06;
  }
  .back-mark {
    position: absolute; left: 0; right: 0; top: 138px;
    display: flex; flex-direction: column; align-items: center;
  }
  .back-mark__name {
    font-family: "Roboto", Arial, sans-serif;
    font-weight: 700; font-size: 44px; letter-spacing: -1px;
    color: var(--on-dark); line-height: 1;
  }
  .back-mark__strapline {
    align-self: flex-end; margin-right: 146px; margin-top: 2px;
    font-family: "Roboto", Arial, sans-serif;
    font-size: 13px; color: var(--on-dark); text-transform: uppercase;
  }
</style>
</head>
<body>
<main class="canvas">

  <section class="card card--front" aria-label="Card front">
    <div class="wordmark">
      <span class="wordmark__dot"></span>
      <span class="wordmark__name">BrightNestMums</span>
    </div>

    <div class="person">
      <p class="person__name">Lena Forbisher</p>
      <p class="person__role">Founder</p>
    </div>

    <p class="address">47 Kowhai Terrace,<br>Ellerslie, Auckland<br>1051, New Zealand.</p>

    <ul class="contacts">
      <li>
        <svg viewBox="0 0 24 24" aria-hidden="true"><path d="M6.6 10.8a15.1 15.1 0 0 0 6.6 6.6l2.2-2.2c.3-.3.7-.4 1-.2 1.1.4 2.3.6 3.6.6.6 0 1 .4 1 1V20c0 .6-.4 1-1 1A17 17 0 0 1 3 4c0-.6.4-1 1-1h3.5c.6 0 1 .4 1 1 0 1.3.2 2.5.6 3.6.1.3 0 .7-.2 1z"/></svg>
        <span>+64 (0)9 571 4860</span>
      </li>
      <li>
        <svg viewBox="0 0 24 24" aria-hidden="true"><path d="M7 1h10a2 2 0 0 1 2 2v18a2 2 0 0 1-2 2H7a2 2 0 0 1-2-2V3a2 2 0 0 1 2-2zm0 3v14h10V4zm5 15.5a1.2 1.2 0 1 0 0 2.4 1.2 1.2 0 0 0 0-2.4z"/></svg>
        <span>021 483 517</span>
      </li>
      <li>
        <svg viewBox="0 0 24 24" aria-hidden="true"><path d="M12 2a10 10 0 1 0 0 20 10 10 0 0 0 0-20zm-1 17.9A8 8 0 0 1 4.2 10.2L9 15v1a2 2 0 0 0 2 2zm6.9-2.5A2 2 0 0 0 16 16h-1v-3a1 1 0 0 0-1-1H8v-2h2a1 1 0 0 0 1-1V7h2a2 2 0 0 0 2-2v-.4a8 8 0 0 1 2.9 12.8z"/></svg>
        <span>BrightNestMums.example</span>
      </li>
    </ul>

    <div class="feature-circle"></div>
  </section>

  <section class="card card--back" aria-label="Card back">
    <div class="back-circle"></div>
    <div class="back-mark">
      <span class="back-mark__name">BrightNestMums</span>
      <span class="back-mark__strapline">Tap; Gather; Sorted</span>
    </div>
  </section>

</main>
</body>
</html>
```